Birchline Septic Solutions

Would like to see some single sided ones but would also like to see some double sided with one sided only being the logo. Owners name is Colin Vandro. Phone number is 555-214-0387
Services are pumping, inspections, installs, and repairs

Contact Information for Business Card

555-241-0387 Colin Vandro Millbrook, OH

```html
<!DOCTYPE html>
<html lang="en">
<head>
<meta charset="utf-8">
<title>Birchline Septic Solutions – Business Cards</title>
<link rel="stylesheet" href="https://fonts.googleapis.com/css2?family=Montserrat:wght@400;500;700;800&display=swap">
<style>
  :root {
    --teal: #06b9b3;
    --ink: #111111;
    --paper: #ffffff;
    --backdrop: #d9d9d9;
  }
  * { box-sizing: border-box; margin: 0; padding: 0; }
  html, body { width: 1200px; height: 856px; overflow: hidden; }
  body {
    background: var(--backdrop);
    font-family: "Montserrat", Arial, sans-serif;
    position: relative;
  }
  .card {
    position: absolute;
    width: 540px;
    height: 309px;
    top: 273px;
    overflow: hidden;
    box-shadow: 0 10px 28px rgba(0,0,0,0.28);
  }
  .card--front { left: 40px; background: var(--paper); }
  .card--back { left: 620px; background: var(--teal); color: var(--paper); }

  .swoosh { position: absolute; inset: 0; width: 100%; height: 100%; }

  .wordmark {
    font-weight: 800;
    text-transform: uppercase;
    line-height: 1.05;
    letter-spacing: 0.04em;
    white-space: nowrap;
  }
  .wordmark .wordmark__line--small {
    display: block;
    font-size: 0.5em;
    letter-spacing: 0.16em;
    margin-top: 6px;
  }
  .card--front .wordmark {
    position: absolute;
    left: 34px;
    top: 96px;
    color: var(--ink);
    font-size: 30px;
    z-index: 1;
  }

  .contact {
    position: absolute;
    right: 20px;
    top: 118px;
    text-align: right;
    color: var(--paper);
    z-index: 1;
  }
  .contact__name { font-weight: 800; font-size: 16px; letter-spacing: 0.02em; text-transform: uppercase; }
  .contact__role { font-size: 12px; font-weight: 500; margin-bottom: 14px; }
  .contact__line { font-size: 12.5px; font-weight: 500; line-height: 1.5; }
  .contact__line svg { width: 11px; height: 11px; vertical-align: -1px; margin-left: 4px; }

  .card--back .wordmark {
    position: absolute;
    left: 0; right: 0;
    top: 84px;
    text-align: center;
    font-size: 40px;
  }
  .card--back .wordmark .wordmark__line--small { letter-spacing: 0.22em; }
  .services {
    position: absolute;
    left: 0; right: 0;
    top: 208px;
    text-align: center;
    font-size: 16px;
    font-weight: 500;
    line-height: 1.5;
  }
  .tick { width: 14px; height: 14px; vertical-align: -2px; margin: 0 4px 0 6px; }
</style>
</head>
<body>
  <section class="card card--front" aria-label="Business card front">
    <svg class="swoosh" viewBox="0 0 540 309" preserveAspectRatio="none" aria-hidden="true">
      <path d="M0 240 C330 260 370 40 540 45 L540 309 L0 309 Z" fill="#06b9b3"/>
      <path d="M0 240 C330 260 370 40 540 45" transform="translate(-12 0)" fill="none" stroke="#111111" stroke-width="8"/>
      <path d="M0 240 C330 260 370 40 540 45" transform="translate(-24 0)" fill="none" stroke="#06b9b3" stroke-width="3"/>
    </svg>
    <div class="wordmark">Birchline<span class="wordmark__line--small">Septic Solutions</span></div>
    <div class="contact">
      <p class="contact__name">Colin Vandro</p>
      <p class="contact__role">Owners</p>
      <p class="contact__line">555-214-0387
        <svg viewBox="0 0 24 24" aria-hidden="true"><path fill="#fff" d="M6.6 10.8a15.1 15.1 0 0 0 6.6 6.6l2.2-2.2a1 1 0 0 1 1-.25 11.4 11.4 0 0 0 3.6.57 1 1 0 0 1 1 1V20a1 1 0 0 1-1 1A17 17 0 0 1 3 4a1 1 0 0 1 1-1h3.5a1 1 0 0 1 1 1c0 1.250.2 2.450.57 3.600a1 1 0 0 1-.25 1z"/></svg>
      </p>
      <p class="contact__line">555-241-0387 Colin Vandro</p>
      <p class="contact__line">Millbrook, OH</p>
    </div>
  </section>

  <section class="card card--back" aria-label="Business card back">
    <div class="wordmark">Birchline<span class="wordmark__line--small">Septic Solutions</span></div>
    <div class="services">
      <p><svg class="tick" viewBox="0 0 16 16" aria-hidden="true"><circle cx="8" cy="8" r="6.5" fill="none" stroke="#fff" stroke-width="1.6"/><path d="M4.8 8.2l2.2 2.2 4.2-4.6" fill="none" stroke="#fff" stroke-width="1.8"/></svg>Services are pumping</p>
      <p><svg class="tick" viewBox="0 0 16 16" aria-hidden="true"><circle cx="8" cy="8" r="6.5" fill="none" stroke="#fff" stroke-width="1.6"/><path d="M4.8 8.2l2.2 2.2 4.2-4.6" fill="none" stroke="#fff" stroke-width="1.8"/></svg>inspections<svg class="tick" viewBox="0 0 16 16" aria-hidden="true"><circle cx="8" cy="8" r="6.5" fill="none" stroke="#fff" stroke-width="1.6"/><path d="M4.8 8.2l2.2 2.2 4.2-4.6" fill="none" stroke="#fff" stroke-width="1.8"/></svg>installs<svg class="tick" viewBox="0 0 16 16" aria-hidden="true"><circle cx="8" cy="8" r="6.5" fill="none" stroke="#fff" stroke-width="1.6"/><path d="M4.8 8.2l2.2 2.2 4.2-4.6" fill="none" stroke="#fff" stroke-width="1.8"/></svg>and repairs</p>
    </div>
  </section>
</body>
</html>
```